Website for a financial survey consultancy

WHO WE ARE
We're a niche HR consultancy specialising in salary comparison surveys for the financial asset management industry. We position ourselves as a small, highly responsive organisation with a strong personal relationship with each of our 50+ blue-chip clients.

WHAT WE DO
Our business is 80% surveys (= products), 20% consultancy (= services). The surveys are a set of online products which clients interact with to find the information they are interested in.

WHAT WE WANT
We are completely revising our existing marketing website and need a new up-to-date look and feel for the site. We want you to design 2 web pages
- Home page
- Internal content page

More details below in Must Have Priorities.

REFERENCE SITES
- www.veltramoor.com - nice background image
- www.plimweather.com - ignoring the animations
- www.gasketvale.com
- www.quorbin.com - clean, fresh, styly but prob not corporate enough
- www.dulveropinex.com - spacious, beautiful, slightly dated tho
- www.tambly.co.uk - ignore the colours. Like the simplicity, larger font size (although want to stick with sans-serif fonts for main content)

DELIVERABLES
The final designs should be delivered as one or more PSD files with clearly named layers. All design elements and treatments should be separated out, for example use adjustment layers rather than applied (and subsequently irreversible) adjustments, strokes, shading, etc.

WHAT NEXT
I'll be monitoring the contest every day and can respond to questions fast. You can IM me on Chatterlyne or QBX.

Reason: Hi folks,

I am extending the deadline to this project as I am travelling this week and therefore will not be able to make a final decision until next Monday. I will try and provide further feedback over the course of this week but I am only going to be online occasionally so be prepared to wait a few days for a reply from me.

Thanks for all the designs so far.

Tobias

Target Market(s)

In order of importance, most important first

1. Potential customers - UK & US financial industry HR professionals, short on time. Heard about us already, want to find out more about what we do, confirm relevance for their needs. Core goal - establish credibility: are we properly resourced, will we be around for years to come, are we *real*.

2. Existing customers - UK & US financial industry professionals, short on time, under pressure, want results quickly, minimum faff, expect high quality, slickly presented information. Primary action: login and use surveys.

3. Industry professionals/researchers - probably arriving through blog content, looking to browse and hoover information. Valuable for their ability to spread awareness of who we are amongst their peers.

Industry/Entity Type

Financial

Requirements
Must have
• GENERAL
Style cues - Corporate, professional, financial, stylish, slick, clean, spacious, light
Size - standard 960px grid

NAVIGATION
- [ Home | About us | Surveys | Consulting | Blog ]
- Sub-nav (roll-over dropdown) on About Us, Surveys & Consulting

ALL PAGES
- Site navigation
- Client login (on screen permanently or link to ajaxy in-page pop-up)
- Footer section
- Existing logo (attached)* - this is obviously an important reference point in the design, esp colour

HOME PAGE
- Communicate (link thru to?) survey/consulting split
- Large photo(s)/backdrop (2-3 interchangeable options ideally). Please consider what rights agreement will be necessary for any photos you include in your design.
- Possibly bigger more prominent version of logo
- Strap line/sentence - "Focussed data is the key to success"
- 3 recent blog posts (should look good with and without blog post images)
- Free downloadable PDF research report + supporting blurb

INTERNAL PAGE
- Page title
- Content - typical page will be less than one screenfull
- Level 1 sub-heading
- Level 2 sub-heading
- Bulleted list
- Content supporting image (any image will do - interested in placement, borders (if any), spacing, caption, etc)
- 'Do something' button

* Note: there is some internal debate about this logo at the moment. Some (me) are keen for it to change, some (not me!) are not. If you have an web page design idea/concept that requires an evolution of the logo, go ahead and evolve it. We can explore this further in the design process as necessary, but don't sweat it.
Nice to have
• Values to communicate
- Knowledgeable
- Professional
- Secure
- Personal
- Experienced
- Financial industry specific
- Accurate
- Reliable
Should not have
• - Search box
- Social media links, other than RSS feed button (discrete)

```html
<!DOCTYPE html>
<html lang="en">
<head>
<meta charset="utf-8">
<title>Kelbrin — Home</title>
<link rel="stylesheet" href="https://fonts.googleapis.com/css2?family=Alegreya+Sans:ital,wght@0,400;0,500;0,700;1,400;1,500;1,700&family=Arimo:wght@400&family=Lato:ital,wght@1,400&display=swap">
<style>
  :root {
    --page-bg: #eef0ec;
    --maroon: #580202;
    --maroon-mid: #6b0b0b;
    --maroon-line: #7a1010;
    --logo-panel: #f5f5f4;
    --nav-band: #c6c6c4;
    --nav-sep: #a9a9a7;
    --nav-text: #5a0707;
    --ink: #111111;
    --body-ink: #2a2a2a;
    --rule: #c4c6c2;
    --link: #3a7ad6;
    --muted: #8a8a88;
    --button-face: #f2f2ef;
    --photo-light: #ebe6d8;
    --photo-mid: #cfc6b0;
    --photo-dark: #9c9480;
  }
  * { box-sizing: border-box; margin: 0; padding: 0; }
  html, body { width: 1200px; height: 712px; overflow: hidden; }
  body {
    position: relative;
    background: var(--page-bg);
    font-family: "Alegreya Sans", sans-serif;
    color: var(--ink);
  }
  .abs { position: absolute; }

  /* Header */
  .nav-band { left: 0; top: 0; width: 1200px; height: 73px; }
  .client-login {
    left: 975px; top: 10px; width: 80px; text-align: right;
    font-size: 15px; font-style: italic; font-weight: 700; color: var(--ink);
    text-decoration: none;
  }
  .main-nav { left: 660px; top: 34px; height: 36px; display: flex; }
  .main-nav a {
    display: block; height: 36px; line-height: 36px; padding: 0 13px;
    font-size: 17px; font-style: italic; color: var(--nav-text);
    text-decoration: none; border-right: 1px solid var(--nav-sep);
  }
  .main-nav a.is-current { font-weight: 700; font-size: 19px; color: var(--maroon); padding: 0 15px 0 12px; }
  .main-nav a:last-child { padding-right: 10px; }

  .hero { left: 0; top: 73px; width: 1200px; height: 265px; background: var(--maroon); border-top: 3px solid var(--maroon-line); }
  .hero-photo { left: 530px; top: 73px; width: 670px; height: 265px; }

  .hero-links { left: 335px; top: 152px; width: 195px; }
  .hero-links .rule { height: 1px; background: linear-gradient(90deg, transparent, rgba(255,255,255,.25), transparent); }
  .hero-link {
    display: block; margin: 11px 0 11px 33px; width: 124px; height: 28px; line-height: 28px;
    background: var(--button-face); text-align: center; text-decoration: none;
    font-size: 17px; font-weight: 700; color: var(--maroon-mid);
    box-shadow: 0 1px 2px rgba(0,0,0,.35);
  }

  /* Brand panel */
  .brand-panel {
    left: 133px; top: 0; width: 193px; height: 338px; background: var(--logo-panel);
    box-shadow: 1px 0 3px rgba(0,0,0,.2);
  }
  .brand-name {
    position: absolute; left: 0; top: 146px; width: 193px; text-align: center;
    font-size: 36px; font-weight: 500; color: var(--maroon-mid); letter-spacing: .5px;
  }

  /* Content */
  .strapline { left: 133px; top: 367px; font-size: 32px; font-weight: 500; color: var(--ink); white-space: nowrap; }
  .intro {
    left: 133px; top: 413px; width: 600px; white-space: nowrap;
    font-family: "Lato", sans-serif;
    font-size: 17.5px; font-style: italic; line-height: 28.8px; color: var(--body-ink);
  }
  .report-link {
    left: 133px; top: 559px; width: 268px; height: 48px;
    background: linear-gradient(#fbfbfa, #e9e6e4); border: 1px solid #cfcccb; border-radius: 3px;
    text-decoration: none; display: flex; align-items: center;
  }
  .report-icon { width: 38px; height: 38px; margin: 0 9px 0 5px; background: var(--maroon-mid); flex: none; }
  .report-title { display: block; font-size: 15.5px; font-style: italic; color: #333; line-height: 16px; }
  .report-sub { display: block; font-size: 12px; font-style: italic; color: var(--maroon-mid); line-height: 15px; }

  /* Blog */
  .latest-blog { left: 785px; top: 378px; width: 270px; }
  .latest-blog h2 {
    font-size: 16px; font-style: italic; font-weight: 700; color: #9e0f0f;
    letter-spacing: 1px; padding-bottom: 3px; border-bottom: 1px solid var(--rule);
  }
  .blog-post { border-bottom: 1px solid var(--rule); padding: 8px 0 8px 1px; font-family: "Arimo", sans-serif; font-size: 11px; line-height: 17.5px; color: var(--ink); }
  .blog-post + .blog-post { padding-top: 12px; }
  .blog-post:last-child { border-bottom: 0; }
  .blog-post time a { color: var(--link); text-decoration: underline; }

  /* Footer */
  .footer { left: 133px; top: 619px; width: 922px; border-top: 1px solid var(--rule); padding-top: 12px; display: flex; justify-content: space-between; font-family: "Arimo", sans-serif; font-size: 11.5px; color: var(--muted); }
  .footer a { color: var(--muted); text-decoration: none; }
</style>
</head>
<body>
  <svg class="abs nav-band" width="1200" height="73" viewBox="0 0 1200 73" aria-hidden="true">
    <path d="M0 60 H450 C470 60 478 33 500 33 H1200 V71 H0 Z" fill="var(--nav-band)"/>
    <rect x="0" y="70" width="1200" height="3" fill="var(--maroon-line)"/>
  </svg>

  <a class="abs client-login" href="#">Client login</a>

  <nav class="abs main-nav">
    <a class="is-current" href="#">Home</a>
    <a href="#">About us</a>
    <a href="#">Surveys</a>
    <a href="#">Consulting</a>
    <a href="#">Blog</a>
  </nav>

  <div class="abs hero"></div>

  <svg class="abs hero-photo" width="670" height="265" viewBox="0 0 670 265" role="img" aria-label="Photograph of a row of ornate cream stone townhouse facades">
    <defs>
      <linearGradient id="facade" x1="0" y1="1" x2="1" y2="0">
        <stop offset="0" stop-color="var(--photo-dark)"/>
        <stop offset=".45" stop-color="var(--photo-mid)"/>
        <stop offset="1" stop-color="var(--photo-light)"/>
      </linearGradient>
    </defs>
    <polygon points="10,265 290,0 670,0 670,265" fill="url(#facade)"/>
  </svg>

  <div class="abs hero-links">
    <div class="rule"></div>
    <a class="hero-link" href="#">Surveys</a>
    <div class="rule"></div>
    <a class="hero-link" href="#">Consulting</a>
    <div class="rule"></div>
  </div>

  <div class="abs brand-panel">
    <div class="brand-name">Kelbrin</div>
  </div>

  <h1 class="abs strapline">Focussed data is the key to success</h1>
  <p class="abs intro">It is a long established fact that a reader will be distracted by the readable<br>content of a page when looking at its layout. The point of using Lorem Ipsum<br>is that it has a more-or-less normal distribution of letters, as opposed to using<br>'Content here, content here', making it look like readable English</p>

  <a class="abs report-link" href="#">
    <span class="report-icon"></span>
    <span>
      <span class="report-title">Research report + supporting blurb</span>
      <span class="report-sub">Free downloadable PDF</span>
    </span>
  </a>

  <section class="abs latest-blog">
    <h2>LATEST&nbsp; BLOG</h2>
    <article class="blog-post">
      <p>fact that a reader will be distracted by the readable<br>fact that a reader will be distracted</p>
      <time><a href="#">9:53 AM Fabruary 1, 2011</a></time>
    </article>
    <article class="blog-post">
      <p>fact that a reader will be distracted by the readable<br>fact that a reader will be distracted</p>
      <time><a href="#">9:53 AM Fabruary 1, 2011</a></time>
    </article>
    <article class="blog-post">
      <p>fact that a reader will be distracted by the readable<br>fact that a reader will be distracted</p>
      <time><a href="#">9:53 AM Fabruary 1, 2011</a></time>
    </article>
  </section>

  <footer class="abs footer">
    <span>© 2011 Kelbrin, Inc. All rights reserved.</span>
    <span><a href="#">Terms and Conditions</a> | <a href="#">Privacy Policy</a> || <a href="#">Business Continuity</a></span>
  </footer>
</body>
</html>
```